Business Card Design for BrightvaleMedia.com

--I need a business card design for my company BrightvaleMedia.com

I have attached my logo...I want the brightvale media logo on the front of the business card, and then I want The Quillstone Chief on the back of it with my information.

I would like to see a light colored background as well as a dark colored background

FRONT:
BRIGHTVALE MEDIA LOGO
248 N. Larkmoor
3rd Floor
San Diego CA 92173
www.BrightvaleMedia.com

Advanced Website & App Development
Websites, Apps, Online Voucher Systems

Leading Edge Marketing Services
SMS, VB, SMM, SEM,

BACK:
QUILLSTONE CHIEF LOGO
Dorian Pelletta
The Quillstone Chief
Call Or Text: 619-555-0148
Dorian@QuillstoneChief.example
www.QuillstoneChief.example

Target Market(s)

small business owners

Industry/Entity Type

Business Consultant

Contact Information for Business Card

FRONT:
BRIGHTVALE MEDIA LOGO
248 N. Larkmoor
3rd Floor
San Diego CA 92173
www.BrightvaleMedia.com

SMS, VB, SMM, SEM,

BACK:
QUILLSTONE CHIEF LOGO
Dorian Pelletta
The Quillstone Chief
Dorian@QuillstoneChief.example
www.QuillstoneChief.example

Requirements
Must have
• add this quote on it somewhere, anywhere,preferrably on back
• "The Fastest Way To Success Is To Take Action”
• — Dorian Pelletta, Quillstone Chief
Nice to have
• open
Should not have
• red

```html
<!DOCTYPE html>
<html lang="en">
<head>
<meta charset="utf-8">
<title>Brightvale Media – Business Card</title>
<link rel="stylesheet" href="https://fonts.googleapis.com/css2?family=Open+Sans:ital,wght@0,400;0,600;0,700;1,400&display=swap">
<style>
  :root {
    --backdrop: #4b4b4b;
    --brand-blue: #0b72ab;
    --brand-blue-deep: #1567a6;
    --card-white: #ffffff;
    --text-grey: #555555;
    --text-dark: #3d3d3d;
    --text-soft: #777777;
  }
  * { margin: 0; padding: 0; box-sizing: border-box; }
  html, body {
    width: 1105px;
    height: 1200px;
    overflow: hidden;
    background: var(--backdrop);
    font-family: "Open Sans", Arial, sans-serif;
  }
  .card {
    position: absolute;
    left: 196px;
    width: 720px;
    height: 411px;
    overflow: hidden;
  }
  .card--front { top: 146px; background: var(--brand-blue); color: var(--card-white); }
  .card--back  { top: 602px; background: var(--card-white); }

  .edge-tab { position: absolute; width: 14px; }
  .card--front .edge-tab {
    left: 0; top: 68px; height: 286px;
    background: var(--card-white);
    border-radius: 0 8px 8px 0;
  }
  .card--back .edge-tab {
    right: 0; top: 88px; height: 244px;
    background: var(--brand-blue);
    border-radius: 8px 0 0 8px;
  }

  .brand-name {
    position: absolute;
    white-space: nowrap;
    font-weight: 400;
    letter-spacing: 3px;
  }
  .card--front .brand-name {
    left: 59px; top: 70px;
    font-size: 38px; line-height: 58px;
    color: var(--card-white);
  }
  .info-line {
    position: absolute;
    left: 59px;
    font-size: 19px;
    line-height: 26px;
    white-space: nowrap;
  }
  .info-line--strong { font-weight: 700; }

  .card--back .brand-name {
    right: 69px; top: 86px;
    font-size: 29px; line-height: 44px;
    color: var(--brand-blue-deep);
    text-align: right;
  }
  .person-name {
    position: absolute; right: 69px; top: 174px;
    font-size: 25px; line-height: 34px; font-weight: 600;
    color: var(--brand-blue-deep);
    white-space: nowrap;
  }
  .person-title {
    position: absolute; right: 69px; top: 207px;
    font-size: 19px; line-height: 26px;
    color: var(--text-grey);
    white-space: nowrap;
  }
  .contact-line {
    position: absolute; right: 69px;
    display: flex; align-items: center; gap: 9px;
    font-size: 19px; line-height: 26px;
    color: var(--text-dark);
    white-space: nowrap;
  }
  .contact-icon { width: 17px; height: 17px; flex: none; }

  .quote {
    position: absolute; right: 69px; top: 350px;
    text-align: right;
    color: var(--text-soft);
    white-space: nowrap;
  }
  .quote-text { font-size: 15px; line-height: 20px; font-style: italic; }
  .quote-source { font-size: 13px; line-height: 18px; margin-top: 2px; }
</style>
</head>
<body>

<section class="card card--front" aria-label="Card front">
  <div class="edge-tab"></div>
  <div class="brand-name">BRIGHTVALE MEDIA</div>
  <p class="info-line" style="top:147px">248 N. Larkmoor, 3rd Floor</p>
  <p class="info-line" style="top:173px">San Diego CA 92173</p>
  <p class="info-line info-line--strong" style="top:201px">www.BrightvaleMedia.com</p>
  <p class="info-line" style="top:241px">Advanced Website &amp; App Development</p>
  <p class="info-line" style="top:267px">Websites • Apps • Online Voucher Systems</p>
  <p class="info-line" style="top:307px">Leading Edge Marketing Services</p>
  <p class="info-line" style="top:334px">SMS • VB • SMM • SEM</p>
</section>

<section class="card card--back" aria-label="Card back">
  <div class="edge-tab"></div>
  <div class="brand-name">QUILLSTONE CHIEF</div>
  <p class="person-name">Dorian Pelletta</p>
  <p class="person-title">The Quillstone Chief</p>

  <p class="contact-line" style="top:245px">619-555-0148
    <svg class="contact-icon" viewBox="0 0 24 24" aria-hidden="true"><path fill="#1567a6" d="M6.6 10.8a15.1 15.1 0 0 0 6.6 6.6l2.2-2.2a1 1 0 0 1 1-.25 11.4 11.4 0 0 0 3.6.57 1 1 0 0 1 1 1V20a1 1 0 0 1-1 1A17 17 0 0 1 3 4a1 1 0 0 1 1-1h3.5a1 1 0 0 1 1 1c0 1.25.2 2.450.57 3.57a1 1 0 0 1-.25 1z"/></svg>
  </p>
  <p class="contact-line" style="top:274px">Dorian@QuillstoneChief.example
    <svg class="contact-icon" viewBox="0 0 24 24" aria-hidden="true"><rect x="2" y="5" width="20" height="14" rx="1.5" fill="#1567a6"/><path d="M3 6.5l9 6.5 9-6.5" fill="none" stroke="#fff" stroke-width="1.6"/></svg>
  </p>
  <p class="contact-line" style="top:302px">www.QuillstoneChief.example
    <svg class="contact-icon" viewBox="0 0 24 24" aria-hidden="true"><circle cx="12" cy="12" r="10" fill="#1567a6"/><g fill="none" stroke="#fff" stroke-width="1.4"><ellipse cx="12" cy="12" rx="4" ry="9"/><path d="M3 12h18M5 7h14M5 17h14"/></g></svg>
  </p>

  <blockquote class="quote">
    <p class="quote-text">“The Fastest Way To Success Is To Take Action”</p>
    <p class="quote-source">— Dorian Pelletta, Quillstone Chief</p>
  </blockquote>
</section>

</body>
</html>
```